Tech business card design

We need an amazing business card design for our new business 'Pexla' a marketing tech startup based in Sydney, Australia. We provide an online marketplace for businesses to search and buy advertising media, connect with service providers and learn more about marketing. We wish to communicate 'cool tech', reliability and professionalism and design based around our logo.

Target Market(s)

Business Owners

Contact Information for Business Card

Name
Position
Email Address
Website
Phone Number

Font styles to use
Other font styles liked:
• Avenir & Avenir Next

Colors

Designer to choose colors to be used in the design.

```html
<!DOCTYPE html>
<html lang="en">
<head>
<meta charset="utf-8">
<title>Pexla business card</title>
<link rel="stylesheet" href="https://fonts.googleapis.com/css2?family=Exo+2:wght@400;700;800&display=swap">
<style>
  :root {
    --navy: #0f1040;
    --navy-text: #1a1d55;
    --ink: #2f2f3a;
    --paper: #fbfbfb;
    --backdrop: #3b3430;
  }
  * { box-sizing: border-box; margin: 0; padding: 0; }
  html, body {
    width: 1200px;
    height: 844px;
    overflow: hidden;
    background: var(--backdrop);
    font-family: "Exo 2", sans-serif;
  }
  .stage {
    position: relative;
    width: 1200px;
    height: 844px;
  }
  .card {
    position: absolute;
    top: 262px;
    width: 540px;
    height: 320px;
    border-radius: 3px;
    box-shadow: 0 10px 26px rgba(0,0,0,.45);
    overflow: hidden;
  }
  .card-front { left: 40px; background: var(--paper); }
  .card-back { left: 620px; background: var(--navy); }

  .holder { position: absolute; left: 48px; top: 96px; }
  .holder-name {
    font-weight: 800;
    font-size: 24px;
    letter-spacing: .5px;
    color: var(--navy-text);
    line-height: 1;
  }
  .holder-role {
    font-size: 15px;
    color: var(--ink);
    margin-top: 3px;
  }
  .contact-list {
    list-style: none;
    margin-top: 18px;
  }
  .contact-item {
    display: flex;
    align-items: center;
    gap: 8px;
    font-size: 17px;
    color: var(--ink);
    line-height: 24px;
  }
  .contact-icon { width: 13px; height: 13px; fill: var(--navy-text); flex: none; }

  .stripes { position: absolute; left: 0; top: 243px; }
  .stripe {
    display: block;
    width: 388px;
    height: 6px;
    background: var(--navy);
    margin-bottom: 5px;
  }
  .front-wordmark {
    position: absolute;
    left: 394px;
    top: 204px;
    font-weight: 800;
    font-size: 44px;
    color: var(--navy);
    line-height: 1;
    letter-spacing: -.5px;
  }
  .back-wordmark {
    position: absolute;
    left: 0; right: 0;
    top: 112px;
    text-align: center;
    font-weight: 800;
    font-size: 78px;
    color: #ffffff;
    line-height: 1;
    letter-spacing: -1px;
  }
</style>
</head>
<body>
<main class="stage">
  <section class="card card-front" aria-label="Card front">
    <div class="holder">
      <h1 class="holder-name">MARCUS REED</h1>
      <p class="holder-role">Managing Director</p>
      <ul class="contact-list">
        <li class="contact-item">
          <svg class="contact-icon" viewBox="0 0 16 16" aria-hidden="true"><path d="M3 1h3l1.5 4-2 1.3a9 9 0 0 0 4.2 4.2L11 8.5l4 1.5v3a2 2 0 0 1-2 2A13 13 0 0 1 1 3a2 2 0 0 1 2-2z"/></svg>
          044-987 654 321
        </li>
        <li class="contact-item">
          <svg class="contact-icon" viewBox="0 0 16 16" aria-hidden="true"><path d="M1 3h14v10H1z M2 4l6 5 6-5" fill="none" stroke="currentColor"/><path d="M1 3h14v1.2L8 10 1 4.2z M1 5.5l4.5 3.7L1 12.5z M15 5.5l-4.5 3.7 4.5 3.3z M1 13l5.3-3.3L8 11l1.7-1.3L15 13z"/></svg>
          hello@pexlamail.com
        </li>
        <li class="contact-item">
          <svg class="contact-icon" viewBox="0 0 16 16" aria-hidden="true"><circle cx="8" cy="8" r="7"/><path d="M5 4c2 1 1 3 3 3s1 3 0 4M10 3c-1 2 2 2 3 3" stroke="#fff" stroke-width="1.2" fill="none"/></svg>
          www.pexlamedia.com
        </li>
      </ul>
    </div>
    <div class="stripes" aria-hidden="true">
      <span class="stripe"></span>
      <span class="stripe"></span>
    </div>
    <p class="front-wordmark">Pexla</p>
  </section>

  <section class="card card-back" aria-label="Card back">
    <p class="back-wordmark">Pexla</p>
  </section>
</main>
</body>
</html>
```